NEW Wordpress Website Design for a Dynamic Long Term Healthcare Company in Hawaii

I would like a new website design for my current company, Marlow Health Collective, which has two different brands - Marlow Homecare and Marlow Senior Living. You can see the current website at www.marlowhealth-example.com. The website should be built using Wordpress Software and the Framewise theme. The website should have a local Hawaii island/tropical feel, but look professional for healthcare. I'm looking for something fresh, and want the designer to select colors, styles, etc.

In the Header, on all pages, I would like a menu that includes Home Care, Senior Living, Rates, and About Us.
Under each of the Header Menu Titles, I would like these drop downs included:
Home Care (drop down pages)- Nurse Aide Care, 24-Hour Home Care, Skilled Nursing, Lifestyle Aide, Hospice at Home, Bathing & Meal Service.
Senior Living (drop down pages) - Long-Term Stay, Short-Term Stay.
Rates (drop down page) - Rates.
About Us (drop down pages) - Our Mission, Ohana Talk, About Dana Marlow.

In the footer, on all pages, you should include the address: 248 Pueo Lane, Suite 310, Honolulu, HI 96817. Phone number: 808-555-0172
The footer should also include buttons for a page called Learn, Caregiver Jobs, and each of the service page links to include: Nurse Aide Care, 24-Hour Home Care, Skilled Nursing, Lifestyle Aide, Hospice at Home, Bathing & Meal Service.
Please don't take the current website and redesign a few aspects. I'm looking for a completely different look and feel.

Target Market(s)

40-80 year olds

Industry/Entity Type

Long Term Healthcare

Coding

Coded - Design and coding required

Requirements
Should not have
• Our existing website as a template. We are looking for a complete redesign. Thank you.

```html
<!DOCTYPE html>
<html lang="en">
<head>
<meta charset="utf-8">
<title>Marlow Health Collective — Homecare &amp; Senior Living</title>
<link rel="stylesheet" href="https://fonts.googleapis.com/css2?family=Marcellus&family=Nunito+Sans:wght@400;600;700;800&display=swap">
<style>
:root{
  --plum:#a8336f;
  --plum-deep:#8e2a5e;
  --pink:#f4899f;
  --pink-soft:#f9c6d3;
  --teal:#72d9da;
  --orange:#ef9a1c;
  --ink:#1f1f24;
  --text:#3a3a40;
  --white:#ffffff;
  --serif:'Marcellus', Georgia, serif;
  --sans:'Nunito Sans', Arial, sans-serif;
}
*{box-sizing:border-box;margin:0;padding:0}
html,body{width:1200px;height:4237px;overflow:hidden}
body{position:relative;background:var(--white);font-family:var(--sans);color:var(--text)}
.abs{position:absolute}
.btn{position:absolute;display:flex;align-items:center;justify-content:center;gap:6px;border-radius:24px;color:var(--white);font:800 13px var(--sans);letter-spacing:.6px;text-transform:uppercase}
.btn::after{content:"›";font-size:18px;line-height:1;margin-top:-2px}
.btn-pink{background:var(--pink)}
.btn-teal{background:var(--teal)}
.btn-plum{background:var(--plum)}
.heading{font-family:var(--serif);font-weight:400;color:var(--ink)}
.rule{position:absolute;width:72px;height:8px;border-top:2px solid var(--plum);border-bottom:2px solid var(--plum)}
.photo{position:absolute}
.brand{font-family:var(--serif);color:var(--plum);display:flex;align-items:center;gap:10px}
.brand .dot{width:34px;height:34px;border-radius:8px;background:var(--pink)}

/* header */
.site-header{position:absolute;left:0;top:0;width:1200px;height:90px;z-index:5}
.site-header .brand{position:absolute;left:118px;top:16px;font-size:34px}
.nav{position:absolute;left:376px;top:32px;display:flex;gap:40px;font:700 13px var(--sans);color:var(--ink)}
.nav span::after{content:" ⌄";color:#999}
.header-phone{position:absolute;left:908px;top:24px;display:flex;align-items:center;gap:10px;font:800 18px var(--sans);color:var(--ink)}
.icon-circle{width:34px;height:34px;border-radius:50%;background:var(--pink);display:flex;align-items:center;justify-content:center}

/* hero */
.hero{position:absolute;left:0;top:0;width:1200px;height:686px;background:linear-gradient(90deg,#f3f4ec 0%,#eef0dc 40%,#e6e9b8 100%)}
.hero-photo{left:520px;top:90px;width:680px;height:596px;background:linear-gradient(135deg,#e9ec9c 0%,#d9d27a 35%,#6aa9c9 65%,#c9b88a 100%)}
.hero .eyebrow{left:107px;top:200px;font:600 17px var(--sans);color:var(--teal);letter-spacing:.5px}
.hero h1{position:absolute;left:107px;top:222px;font-size:70px;line-height:68px}
.hero p{left:110px;top:374px;width:360px;font-size:16px;line-height:23px}

/* mission */
.mission{position:absolute;left:0;top:686px;width:1200px;height:455px;background:linear-gradient(90deg,#b03a78,#a7366f 70%,#c47a9a)}
.mission h2{position:absolute;left:0;width:1200px;top:62px;text-align:center;color:var(--white);font-size:52px}
.mission .rule{left:560px;top:130px;border-color:var(--white);width:80px}
.mission p{position:absolute;left:200px;top:163px;width:800px;text-align:center;color:var(--white);font-size:17px;line-height:30px}
.btn-outline{border:2px solid var(--white);background:transparent;font-size:16px;border-radius:30px}

/* services */
.service-img{border-radius:40px 40px 0 0;overflow:hidden}
.photo-band{position:absolute;height:14px;border-radius:0 0 14px 14px}
.service h2{position:absolute;font-size:52px}
.service p{position:absolute;font-size:17px;line-height:26px}
.checks{position:absolute;list-style:none;font:800 15px var(--sans);color:var(--ink);letter-spacing:.3px}
.checks li{position:relative;padding-left:24px;height:38px}
.checks li::before{content:"›";position:absolute;left:2px;top:-6px;font-size:24px;color:var(--orange)}
.scenery{left:0;top:1610px;width:1200px;height:270px;background:linear-gradient(180deg,rgba(255,255,255,0) 0%,#eef1e6 40%,#f2f3ee 100%)}

/* rates */
.rates{position:absolute;left:0;top:2443px;width:1200px;height:697px;background:linear-gradient(90deg,#fbd3e1,#f6c0d4 50%,#f5d7e4)}
.rates-photo{left:0;top:2737px;width:1200px;height:403px;background:linear-gradient(90deg,#6d8a4a 0%,#c8c59c 25%,#d6a48a 55%,#c9b89a 80%,#9bb3a8 100%);border-bottom-right-radius:220px}
.rates h2{position:absolute;left:0;width:1200px;top:62px;text-align:center;font-size:54px}
.rates .rule{left:564px;top:130px;border-color:var(--orange);width:72px}
.rates p{position:absolute;left:230px;top:159px;width:740px;text-align:center;font-size:18px;line-height:30px}

/* contact */
.contact-bg{left:0;top:3140px;width:1200px;height:608px;background:linear-gradient(180deg,#ffffff 0%,#f4f7f4 35%,#cfeef0 75%,#9fdde3 100%)}
.contact h2{position:absolute;left:135px;top:3250px;font-size:52px}
.contact .rule{left:137px;top:3323px}
.contact p{position:absolute;left:135px;top:3356px;width:440px;font-size:17px;line-height:26px}
.info{position:absolute;left:138px;display:flex;align-items:center;gap:18px;font-size:20px;color:var(--ink);line-height:24px}
.info .icon-circle{width:46px;height:46px;background:var(--plum)}
.info strong{font-weight:800;font-size:22px}
.form-card{position:absolute;left:595px;top:3247px;width:538px;height:416px;background:var(--pink);border-radius:30px 30px 30px 0}
.field{position:absolute;background:var(--white);border:1px solid #e6e6e6;padding:0 16px;display:flex;align-items:center;font:600 14px var(--sans);color:#444}
.field.area{align-items:flex-start;padding-top:12px}

/* footer */
.footer-curve{left:0;top:3740px;width:1200px;height:120px}
.footer .brand{position:absolute;left:145px;top:3830px;font-size:38px}
.footer-btn{position:absolute;left:155px;width:182px;height:36px;display:flex;align-items:center;justify-content:center;font:800 12px var(--sans);color:var(--white);letter-spacing:.5px}
.social{position:absolute;top:4022px;width:30px;height:30px;border-radius:50%;background:var(--plum)}
.footer-col{position:absolute;top:3828px}
.footer-col h3{font-family:var(--serif);font-size:24px;font-weight:400;color:var(--ink);border-left:2px solid var(--plum);padding-left:14px;margin-left:-16px;line-height:24px;margin-bottom:12px}
.footer-col ul{list-style:none;font-size:15px;line-height:31px;color:var(--text)}
.footer-contact{display:flex;gap:12px;align-items:center;font-size:13px;line-height:16px;color:var(--ink);margin-bottom:14px}
.footer-contact .icon-circle{width:30px;height:30px;background:var(--plum);flex:none}
.sub-brand{position:absolute;top:4020px;font-family:var(--serif);font-size:26px;color:var(--plum);display:flex;align-items:center;gap:6px}
.sub-brand .dot{width:16px;height:16px;border-radius:4px;background:var(--pink)}
.divider{left:20px;top:4131px;width:1160px;height:1px;background:#e5e5e5}
.copyright{position:absolute;left:0;top:4153px;width:1200px;text-align:center;font-size:13px;color:var(--text)}
.copyright u{color:var(--ink)}
</style>
</head>
<body>

<section class="hero">
  <div class="photo hero-photo" role="img" aria-label="Caregiver in scrubs helping an elderly man dress while seated on a bed"></div>
  <svg class="abs" style="left:0;top:0" width="1200" height="686" aria-hidden="true">
    <defs><linearGradient id="fadeL" x1="0" x2="1"><stop offset="0" stop-color="#f3f4ec"/><stop offset="1" stop-color="#f3f4ec" stop-opacity="0"/></linearGradient></defs>
    <rect x="520" y="90" width="160" height="596" fill="url(#fadeL)"/>
    <path d="M1200 480 C1190 600 1120 672 1000 686 L1200 686 Z" fill="#a8336f"/>
    <rect x="0" y="0" width="1200" height="90" fill="#ffffff" opacity=".7"/>
  </svg>
  <div class="abs eyebrow">MARLOW HEALTH COLLECTIVE</div>
  <h1 class="heading">Homecare &amp;<br>Senior Living</h1>
  <p class="abs">Marlow Homecare provides a variety of professional in-home health care services throughout the entire island of Oahu.</p>
  <div class="btn btn-pink" style="left:110px;top:469px;width:173px;height:44px">View Rates</div>
  <div class="btn btn-teal" style="left:301px;top:469px;width:174px;height:44px">Contact Us</div>
</section>

<header class="site-header">
  <div class="brand"><span class="dot"></span>Marlow</div>
  <nav class="nav"><span>HOME CARE</span><span>SENIOR LIVING</span><span>RATES</span><span>ABOUT US</span></nav>
  <div class="header-phone">
    <span class="icon-circle"><svg width="16" height="16" viewBox="0 0 24 24"><path fill="#fff" d="M6.6 10.8a15 15 0 0 0 6.6 6.6l2.2-2.2c.3-.3.7-.4 1-.2 1.1.4 2.3.6 3.6.6.6 0 1 .4 1 1V20c0 .6-.4 1-1 1A17 17 0 0 1 3 4c0-.6.4-1 1-1h3.5c.6 0 1 .4 1 1 0 1.3.2 2.5.6 3.6.1.3 0 .7-.2 1z"/></svg></span>
    808-555-0172
  </div>
</header>

<section class="mission">
  <h2 class="heading">Our Mission</h2>
  <div class="rule"></div>
  <p>At Marlow Health Collective, our mission is to provide compassionate and professional long-term healthcare services that empower individuals to maintain their highest level of independence, health, and well-being in the comfort of their own homes or ours, either through our licensed home healthcare agency</p>
  <div class="btn btn-outline" style="left:495px;top:302px;width:210px;height:54px">View Rates</div>
</section>
<svg class="abs" style="left:0;top:1141px" width="1200" height="200" aria-hidden="true">
  <path d="M0 0 L260 0 C120 0 0 60 0 200 Z" fill="#a8336f"/>
</svg>

<div class="photo scenery" role="img" aria-label="Faint misty view of green Hawaiian mountains above the sea"></div>
<section class="service">
  <div class="photo service-img" style="left:72px;top:1261px;width:526px;height:420px;background:linear-gradient(135deg,#c9b97a,#8a6a45 45%,#3e6fb6 70%,#c7b79a)" role="img" aria-label="Caregiver and client chatting on a leather sofa in a bright living room"></div>
  <div class="photo-band" style="left:72px;top:1681px;width:526px;background:var(--pink)"></div>
  <h2 class="heading" style="left:659px;top:1286px">Home Care</h2>
  <div class="rule" style="left:662px;top:1356px"></div>
  <p style="left:659px;top:1382px;width:460px">Marlow Homecare understands that every person's care journey is unique. We tailor our in-home services to meet the diverse nurturing experience</p>
  <ul class="checks" style="left:662px;top:1484px;width:220px"><li>NURSE AIDE CARE</li><li>24-HOUR HOME CARE</li><li>SKILLED NURSING</li></ul>
  <ul class="checks" style="left:889px;top:1484px;width:260px"><li>LIFESTYLE AIDE</li><li>HOSPICE AT HOME</li><li>BATHING &amp; MEAL SERVICE</li></ul>
  <div class="btn btn-pink" style="left:656px;top:1624px;width:184px;height:48px">Learn More</div>
</section>

<section class="service">
  <h2 class="heading" style="left:117px;top:1918px">Senior Living</h2>
  <div class="rule" style="left:120px;top:1990px"></div>
  <p style="left:117px;top:2020px;width:440px">Marlow Senior Living creates a warm, supportive, and enriching care home environment where seniors can thrive in their golden years. We provide residential care that promotes well-being, connection, and dignity of each individual.</p>
  <ul class="checks" style="left:114px;top:2177px;width:240px;font-size:17px"><li style="height:35px">LONG-TERM STAY</li><li>SHORT-TERM STAY</li></ul>
  <div class="btn btn-teal" style="left:112px;top:2259px;width:186px;height:48px">Learn More</div>
  <div class="photo service-img" style="left:607px;top:1886px;width:526px;height:420px;background:linear-gradient(135deg,#e8d77a,#b4823a 40%,#d94a3a 60%,#4a7ab8 75%,#7a5f48)" role="img" aria-label="Group of seniors doing a light dumbbell exercise class with an instructor"></div>
  <div class="photo-band" style="left:607px;top:2306px;width:526px;background:var(--teal)"></div>
</section>

<section class="rates">
  <h2 class="heading">Rates &amp; Pricing</h2>
  <div class="rule"></div>
  <p>Lorem ipsum dolor sit amet, consectetur adipiscing elit, sed do eiusmod tempor incididunt ut labore et dolore magna aliqua.</p>
  <div class="btn btn-pink" style="left:518px;top:230px;width:184px;height:46px">Learn More</div>
</section>
<div class="photo rates-photo" role="img" aria-label="Three women laughing while knitting colorful yarn on a sofa"></div>

<div class="photo contact-bg" role="img" aria-label="Soft tropical beach with turquoise water and palm trees"></div>
<section class="contact">
  <h2 class="heading">Contact Us</h2>
  <div class="rule"></div>
  <p>Lorem ipsum dolor sit amet, consectetur adipiscing elit, sed do eiusmod tempor incididunt ut labore et dolore magna aliqua.</p>
  <div class="info" style="top:3473px">
    <span class="icon-circle"><svg width="20" height="24" viewBox="0 0 24 24"><path fill="#fff" d="M12 2a7 7 0 0 0-7 7c0 5 7 13 7 13s7-8 7-13a7 7 0 0 0-7-7zm0 9.5A2.5 2.5 0 1 1 12 6.5a2.5 2.5 0 0 1 0 5z"/></svg></span>
    <span>248 Pueo Lane, Suite 310,<br>Honolulu, HI 96817</span>
  </div>
  <div class="info" style="top:3554px">
    <span class="icon-circle"><svg width="20" height="20" viewBox="0 0 24 24"><path fill="#fff" d="M6.6 10.8a15 15 0 0 0 6.6 6.6l2.2-2.2c.3-.3.7-.4 1-.2 1.1.4 2.3.6 3.6.6.6 0 1 .4 1 1V20c0 .6-.4 1-1 1A17 17 0 0 1 3 4c0-.6.4-1 1-1h3.5c.6 0 1 .4 1 1 0 1.3.2 2.5.6 3.6.1.3 0 .7-.2 1z"/></svg></span>
    <span>Phone number<br><strong>808-555-0172</strong></span>
  </div>
  <div class="form-card">
    <div class="field" style="left:51px;top:66px;width:219px;height:49px">First Name</div>
    <div class="field" style="left:278px;top:66px;width:219px;height:49px">Last Name</div>
    <div class="field" style="left:51px;top:128px;width:219px;height:49px">Email address</div>
    <div class="field" style="left:278px;top:128px;width:219px;height:49px">Phone Number</div>
    <div class="field area" style="left:51px;top:192px;width:446px;height:112px">Message</div>
    <div class="btn btn-plum" style="left:58px;top:320px;width:204px;height:50px;border-radius:26px">Send Message</div>
  </div>
</section>

<svg class="abs footer-curve" width="1200" height="120" aria-hidden="true">
  <path d="M0 120 C0 40 60 8 160 8 L1200 8 L1200 120 Z" fill="#ffffff"/>
</svg>
<footer class="footer">
  <div class="abs" style="left:0;top:3860px;width:1200px;height:377px;background:#fff"></div>
  <div class="brand"><span class="dot"></span>Marlow</div>
  <div class="footer-btn" style="top:3916px;background:var(--teal);color:var(--plum-deep)">LEARN</div>
  <div class="footer-btn" style="top:3965px;background:var(--pink)">CARE GIVER JOBS</div>
  <span class="social" style="left:177px"></span>
  <span class="social" style="left:215px"></span>
  <span class="social" style="left:253px"></span>
  <span class="social" style="left:291px"></span>

  <div class="footer-col" style="left:420px">
    <h3>Navigation</h3>
    <ul><li>Home Care</li><li>Senior Living</li><li>Rates</li><li>About Us</li></ul>
  </div>
  <div class="footer-col" style="left:628px">
    <h3>Services</h3>
    <ul><li>Nurse Aide Care</li><li>24-Hour Home Care</li><li>Skilled Nursing</li><li>Lifestyle Aide</li><li>Hospice at Home</li><li>Bathing &amp; Meal Service</li></ul>
  </div>
  <div class="footer-col" style="left:855px">
    <h3>Contact Us</h3>
    <div class="footer-contact"><span class="icon-circle"><svg width="14" height="16" viewBox="0 0 24 24"><path fill="#fff" d="M12 2a7 7 0 0 0-7 7c0 5 7 13 7 13s7-8 7-13a7 7 0 0 0-7-7zm0 9.5A2.5 2.5 0 1 1 12 6.5a2.5 2.5 0 0 1 0 5z"/></svg></span><span>248 Pueo Lane, Suite 310,<br>Honolulu, HI 96817</span></div>
    <div class="footer-contact"><span class="icon-circle"><svg width="14" height="14" viewBox="0 0 24 24"><path fill="#fff" d="M6.6 10.8a15 15 0 0 0 6.6 6.6l2.2-2.2c.3-.3.7-.4 1-.2 1.1.4 2.3.6 3.6.6.6 0 1 .4 1 1V20c0 .6-.4 1-1 1A17 17 0 0 1 3 4c0-.6.4-1 1-1h3.5c.6 0 1 .4 1 1 0 1.3.2 2.5.6 3.6.1.3 0 .7-.2 1z"/></svg></span><span>Phone number<br><strong>808-555-0172</strong></span></div>
  </div>
  <div class="sub-brand" style="left:868px"><span class="dot"></span>Marlow</div>
  <div class="sub-brand" style="left:995px;color:#3aa9ad"><span class="dot" style="background:var(--teal)"></span>Marlow</div>

  <div class="abs divider"></div>
  <div class="copyright">Copyright © 2024 <u>Marlow Health Collective</u>. All Right Reserved</div>
</footer>

</body>
</html>
```